Australian Based Web Development Company Needs a Fresh New Modern Look (logo and responsive website)

We are Coral Web Development, an Australian based web development company looking to give our company a fresh, new and modern look.

We tend to deal with small to medium sized businesses, and want to convey the message that we are professional and capable of developing a solution to any need or problem.

Our specialty is custom development applications, such as, intranets, integration software, and client portals.

We have recently started mobile application development as well (iOS and Android).

You can view our current logo and website on https://www.coralwebdevelopment.example/

As we are looking for both a logo and a website design, we may decide to have the website design completed by a different designer to the winning logo designer.

Target Market(s)

Small to medium enterprise businesses

Industry/Entity Type

It Company

Logo Text

Coral Web Development

Number of Pages Required

2 page

Logo styles of interest
Abstract Logo
Wordmark Logo
Font styles to use
Sans Serif

Colors
85cae6
33b8a4

Requirements
Must have
• Website design - a responsive layout (960-1000px content width), and background image/texture of 2,560px wide. A home page design, and a generic content page design.
• Colours - we like blues, greens (more blue-green like teal) and grey, but we are open to seeing other colours if you feel appropriate.
Nice to have
• Website design - Two websites I like the design style is http://www.mavonstack.example/ and https://www.pilvo.example/au/accounting-software/

```html
<!DOCTYPE html>
<html lang="en">
<head>
<meta charset="utf-8">
<title>Coral Web Development – Mobile Home</title>
<link rel="stylesheet" href="https://fonts.googleapis.com/css2?family=Open+Sans:wght@300;400;600;700&family=Oswald:wght@500&display=swap">
<style>
  :root {
    --canvas-bg: #e6e9eb;
    --screen-bg: #ffffff;
    --teal: #5fd0c0;
    --teal-deep: #33b8a4;
    --sky: #85cae6;
    --ink: #3a3f44;
    --ink-soft: #7b8187;
    --ink-muted: #9aa0a5;
    --rule: #c9cdd0;
  }
  * { box-sizing: border-box; margin: 0; padding: 0; }
  html, body {
    width: 1200px; height: 804px; overflow: hidden;
    background: var(--canvas-bg);
    font-family: "Open Sans", Arial, sans-serif;
  }
  .mobile-page {
    position: absolute; left: 390px; top: 12px;
    width: 420px; height: 780px;
    background: var(--screen-bg);
    overflow: hidden;
    text-align: center;
  }
  .service-badge {
    position: relative; width: 150px; height: 110px; margin: 0 auto;
  }
  .service-badge svg { display: block; }
  .service-caption {
    margin-top: 10px;
    font-size: 14px; line-height: 1.35; color: var(--ink-soft);
  }
  .section-title {
    margin-top: 30px;
    font-size: 27px; color: var(--ink); font-weight: 700; letter-spacing: .3px;
  }
  .section-title .light { font-weight: 300; color: var(--ink-muted); }
  .portfolio-visual {
    width: 320px; height: 190px; margin: 26px auto 0;
    background: linear-gradient(160deg, #f4f7fa 0%, #d9e9f3 55%, #a9cfe6 100%);
  }
  .project-title {
    margin-top: 30px;
    font-family: "Oswald", "Arial Narrow", sans-serif;
    font-weight: 500; font-size: 24px; letter-spacing: .5px;
    color: var(--ink);
  }
  .project-text {
    width: 330px; margin: 14px auto 0;
    font-size: 12px; line-height: 1.7; color: var(--ink-soft);
  }
  .learn-more {
    display: inline-block; margin-top: 24px;
    padding: 12px 30px;
    border: 1px solid var(--rule); border-radius: 4px;
    font-size: 13px; letter-spacing: 1px; color: var(--ink-soft);
    text-decoration: none; text-transform: uppercase;
  }
  .next-visual {
    width: 320px; height: 140px; margin: 34px auto 0;
    background: linear-gradient(180deg, #eef3f6 0%, #c8dbe6 100%);
  }
</style>
</head>
<body>
  <main class="mobile-page">
    <section class="service">
      <div class="service-badge">
        <svg width="150" height="110" viewBox="0 0 150 110" aria-hidden="true">
          <circle cx="75" cy="30" r="66" fill="none" stroke="var(--teal)" stroke-width="10"/>
          <rect x="58" y="30" width="34" height="40" rx="3" fill="#8d9398"/>
          <rect x="63" y="36" width="10" height="10" fill="#fff"/>
          <rect x="77" y="36" width="10" height="10" fill="#fff"/>
          <rect x="63" y="50" width="24" height="4" fill="#fff"/>
        </svg>
      </div>
      <p class="service-caption">Lumo Phone &amp; Lumo Tab<br>Applications</p>
    </section>

    <section class="portfolio">
      <h2 class="section-title">Featured <span class="light">Portfolio</span></h2>
      <div class="portfolio-visual" role="img" aria-label="Illustration of responsive website layouts displayed across desktop and tablet screens"></div>
      <h3 class="project-title">LOREM IPSUM DUMMY</h3>
      <p class="project-text">Contrary to popular belief, Lorem Ipsum is not simply random text. It has roots in a piece of classical Latin literature from 45 BC, making it over 2000 years old.</p>
      <a class="learn-more" href="#">Learn More</a>
      <div class="next-visual" role="img" aria-label="Photo of a modern office workspace for the next portfolio project"></div>
    </section>
  </main>
</body>
</html>
```